holloway paving service

Needs to have phone number 0418259730 and email markholloway@brightmail.com.au.
ABN 62318470915
name mark holloway

For all your concreting solutions
Excavation
Exposed & colour concrete
House & shed slabs
Driveways
Landing & steps

Contact Information for Business Card

ph 0418259730
email markholloway@brightmail.com.au.
ABN 62318470915
name mark holloway

```html
<!DOCTYPE html>
<html lang="en">
<head>
<meta charset="utf-8">
<title>Holloway Paving Service – Business Card</title>
<link rel="stylesheet" href="https://fonts.googleapis.com/css2?family=Lato:wght@300;400;700;900&display=swap">
<style>
  :root {
    --backdrop: #1b1b1b;
    --orange: #f26b21;
    --card-black: #121212;
    --white: #ffffff;
    --grey: #7d7d7d;
    --rule: #5a5a5a;
  }
  * { box-sizing: border-box; margin: 0; padding: 0; }
  html, body {
    width: 1200px; height: 900px; overflow: hidden;
    background: var(--backdrop);
    font-family: "Lato", sans-serif;
  }
  .canvas { position: relative; width: 1200px; height: 900px; }
  .card {
    position: absolute; width: 560px; height: 320px;
    border-radius: 22px; overflow: hidden;
    box-shadow: 0 18px 40px rgba(0,0,0,.55);
  }

  /* Front */
  .card-front { left: 80px; top: 100px; background: var(--orange); color: var(--white); }
  .front-brand {
    position: absolute; left: 150px; top: 60px;
    display: flex; align-items: center; gap: 18px;
  }
  .brand-square { width: 58px; height: 58px; background: var(--white); flex: none; }
  .brand-divider { width: 1.5px; height: 86px; background: var(--white); flex: none; }
  .brand-name {
    font-weight: 700; font-size: 21px; letter-spacing: .5px;
    text-transform: uppercase; line-height: 1.2; max-width: 230px;
  }
  .front-tagline {
    position: absolute; left: 150px; top: 178px;
    font-weight: 300; font-size: 16px; letter-spacing: 1px; text-transform: uppercase;
    white-space: nowrap;
  }
  .service-rows { position: absolute; left: 150px; top: 212px; }
  .service-row {
    list-style: none; display: flex; align-items: center;
    font-size: 15px; font-weight: 400; white-space: nowrap;
    margin-bottom: 12px;
  }
  .service-row li { display: flex; align-items: center; }
  .service-row li + li::before {
    content: ""; width: 8px; height: 8px; margin: 0 12px;
    background: var(--white); transform: rotate(45deg);
  }

  /* Back */
  .card-back { left: 560px; top: 480px; background: var(--card-black); color: var(--white); }
  .back-brand {
    position: absolute; left: 170px; top: 46px;
    display: flex; align-items: center; gap: 16px;
  }
  .back-brand .brand-square { background: var(--orange); width: 54px; height: 54px; }
  .back-brand .brand-divider { background: var(--orange); height: 70px; }
  .back-brand .brand-name { color: var(--orange); font-size: 20px; }
  .back-rule {
    position: absolute; left: 190px; right: 40px; top: 140px;
    height: 1px; background: var(--rule);
  }
  .abn { position: absolute; right: 40px; top: 168px; font-size: 15px; letter-spacing: .5px; }
  .holder {
    position: absolute; left: 36px; right: 40px; top: 212px;
    display: flex; align-items: center; gap: 12px;
  }
  .holder-name { font-weight: 900; font-size: 19px; letter-spacing: .5px; text-transform: uppercase; white-space: nowrap; }
  .holder-name .first { color: var(--orange); }
  .holder-name .last { color: var(--grey); }
  .holder-rule { flex: 1; height: 1px; background: var(--rule); }
  .contact-list { position: absolute; left: 36px; top: 250px; list-style: none; font-size: 16px; }
  .contact-list li { display: flex; align-items: center; gap: 10px; margin-bottom: 6px; }
  .contact-icon { width: 15px; height: 15px; fill: var(--orange); flex: none; }
</style>
</head>
<body>
<main class="canvas">

  <section class="card card-front" aria-label="Business card front">
    <div class="front-brand">
      <span class="brand-square"></span>
      <span class="brand-divider"></span>
      <span class="brand-name">Holloway Paving Service</span>
    </div>
    <p class="front-tagline">For all your concreting solutions</p>
    <div class="service-rows">
      <ul class="service-row">
        <li>Excavation</li>
        <li>Exposed &amp; colour concrete</li>
      </ul>
      <ul class="service-row">
        <li>House &amp; shed slabs</li>
        <li>Driveways</li>
        <li>Landing &amp; steps</li>
      </ul>
    </div>
  </section>

  <section class="card card-back" aria-label="Business card back">
    <div class="back-brand">
      <span class="brand-square"></span>
      <span class="brand-divider"></span>
      <span class="brand-name">Holloway Paving Service</span>
    </div>
    <div class="back-rule"></div>
    <p class="abn">ABN 62318470915</p>
    <div class="holder">
      <span class="holder-name"><span class="first">Mark</span> <span class="last">Holloway</span></span>
      <span class="holder-rule"></span>
    </div>
    <ul class="contact-list">
      <li>
        <svg class="contact-icon" viewBox="0 0 24 24" aria-hidden="true"><path d="M6.6 10.8a15.1 15.1 0 0 0 6.6 6.6l2.2-2.2a1 1 0 0 1 1-.25 11.4 11.4 0 0 0 3.6.57 1 1 0 0 1 1 1V20a1 1 0 0 1-1 1A17 17 0 0 1 3 4a1 1 0 0 1 1-1h3.5a1 1 0 0 1 1 1c0 1.25.2 2.45.57 3.57a1 1 0 0 1-.25 1z"/></svg>
        0418259730
      </li>
      <li>
        <svg class="contact-icon" viewBox="0 0 24 24" aria-hidden="true"><path d="M2 5h20v14H2z M3.5 6.5 12 13l8.5-6.5" stroke="#121212" stroke-width="1.6"/></svg>
        markholloway@brightmail.com.au
      </li>
    </ul>
  </section>

</main>
</body>
</html>
```